RWT Fittings Ltd Business Cards

We need a business card with our business logo. We provide window and door installations on high-rises in west coast British Colombia, Canada.

I would like my business information and details on one side of the card, and the other side the company name with logo

Target Market(s)

General Contractors

Industry/Entity Type

Construction

Contact Information for Business Card

one side i want my company name and logo in the dark theme logo that i provided

Requirements
Must have
• Marco Peltieri, 16045518293, RWTFittings@mailbox-demo.com, 1407-5194 Linden Row Burnaby BC, V5H 2K9, Owner & Manager

```html
<!DOCTYPE html>
<html lang="en">
<head>
<meta charset="UTF-8">
<title>RWT Fittings Ltd Business Cards</title>
<link href="https://fonts.googleapis.com/css2?family=Open+Sans:wght@400;600;700&display=swap" rel="stylesheet">
<style>
  :root {
    --stage: #232325;
    --card-dark: #222226;
    --brand-blue: #27a8e0;
    --name-grey: #a3a3a6;
    --text-light: #ffffff;
    --ink: #121214;
  }
  * { box-sizing: border-box; margin: 0; padding: 0; }
  html, body {
    width: 1200px;
    height: 780px;
    overflow: hidden;
    background: var(--stage);
    font-family: "Open Sans", Arial, sans-serif;
  }
  .sheet {
    width: 1200px;
    height: 780px;
    display: flex;
    align-items: center;
    justify-content: center;
    gap: 40px;
  }
  .card {
    position: relative;
    width: 560px;
    height: 320px;
    overflow: hidden;
  }

  /* Contact side */
  .card--contact { background: var(--card-dark); }
  .edge-bar {
    position: absolute;
    top: 78px;
    width: 8px;
    height: 150px;
    background: var(--brand-blue);
  }
  .edge-bar--left { left: 12px; }
  .edge-bar--right { right: 12px; top: 70px; }
  .brand {
    position: absolute;
    left: 40px;
    top: 118px;
    width: 230px;
    display: flex;
    align-items: center;
    gap: 10px;
  }
  .brand__mark {
    flex: none;
    width: 22px;
    height: 22px;
    background: var(--brand-blue);
  }
  .brand__name {
    font-weight: 700;
    font-size: 24px;
    line-height: 1.1;
    color: var(--brand-blue);
  }
  .divider {
    position: absolute;
    left: 285px;
    top: 55px;
    width: 1px;
    height: 170px;
    background: linear-gradient(to bottom, rgba(255,255,255,0), rgba(255,255,255,0.9) 50%, rgba(255,255,255,0));
  }
  .details {
    position: absolute;
    left: 312px;
    top: 44px;
    right: 24px;
    color: var(--text-light);
  }
  .details__name {
    font-weight: 700;
    font-size: 27px;
    line-height: 1.1;
    white-space: nowrap;
  }
  .details__name .first { color: var(--brand-blue); }
  .details__name .last { color: var(--name-grey); }
  .details__title {
    font-size: 13px;
    margin-top: 3px;
  }
  .contact-list {
    list-style: none;
    margin-top: 22px;
  }
  .contact-list li {
    display: flex;
    align-items: center;
    gap: 8px;
    font-size: 12px;
    line-height: 1.9;
  }
  .contact-list svg { width: 13px; height: 13px; flex: none; }
  .address {
    position: absolute;
    left: 0;
    right: 0;
    bottom: 30px;
    text-align: center;
    color: var(--text-light);
    font-size: 14px;
  }

  /* Brand side */
  .card--brand {
    background: var(--brand-blue);
    display: flex;
    align-items: center;
    justify-content: center;
    gap: 14px;
  }
  .card--brand .brand__mark {
    width: 34px;
    height: 34px;
    background: var(--ink);
  }
  .card--brand .brand__name {
    font-size: 42px;
    color: var(--ink);
  }
</style>
</head>
<body>
<main class="sheet">

  <section class="card card--contact" aria-label="Contact side">
    <span class="edge-bar edge-bar--left"></span>
    <span class="edge-bar edge-bar--right"></span>

    <div class="brand">
      <span class="brand__mark"></span>
      <span class="brand__name">RWT Fittings Ltd</span>
    </div>

    <span class="divider"></span>

    <div class="details">
      <p class="details__name"><span class="first">Marco</span> <span class="last">Peltieri</span></p>
      <p class="details__title">Managing Director</p>
      <ul class="contact-list">
        <li>
          <svg viewBox="0 0 24 24" aria-hidden="true"><path fill="#27a8e0" d="M6.6 10.8a15 15 0 0 0 6.6 6.6l2.2-2.2a1 1 0 0 1 1-.25 11.4 11.4 0 0 0 3.6.57 1 1 0 0 1 1 1V20a1 1 0 0 1-1 1A17 17 0 0 1 3 4a1 1 0 0 1 1-1h3.5a1 1 0 0 1 1 1c0 1.25.2 2.45.57 3.57a1 1 0 0 1-.25 1z"/></svg>
          (604) 551-8293
        </li>
        <li>
          <svg viewBox="0 0 24 24" aria-hidden="true"><rect x="2" y="5" width="20" height="14" rx="1.5" fill="#27a8e0"/><path d="M3 6l9 7 9-7" fill="none" stroke="#222226" stroke-width="1.6"/></svg>
          RWTFittings@mailbox-demo.com
        </li>
        <li>
          <svg viewBox="0 0 24 24" aria-hidden="true"><circle cx="12" cy="12" r="10" fill="#27a8e0"/><path d="M2 12h20M12 2c3 3 3 17 0 20M12 2c-3 3-3 17 0 20" fill="none" stroke="#222226" stroke-width="1.4"/></svg>
          www.rwtfittings-demo.com
        </li>
      </ul>
    </div>

    <p class="address">1407-5194 Linden Row Burnaby BC, V5H 2K9</p>
  </section>

  <section class="card card--brand" aria-label="Brand side">
    <span class="brand__mark"></span>
    <span class="brand__name">RWT Fittings Ltd</span>
  </section>

</main>
</body>
</html>
```